Book Cover on Entrepreneurship for Eye Doctors

Book Title: The Lens Practice Builder: How to launch with confidence
Author: Rufus Tembley, Optom, MBA, DBA, EIC
I need a Book Cover with the following descriptions:
Topic: the book topic is entrepreneurship knowledge for eye care professionals.
The book's audience: eye care professionals who you know as Opticians, who sell eyeglasses and sunglasses;
Optometrists, test eyes, fit contact lenses, and prescribe medication
Ophthalmologists, perform eye surgery
More about the audience:
1- Young eye care professionals who don’t know about entrepreneurship and those who are stuck in the 9-to-5 job;
2- This is the first book written on entrepreneurship with eye care professionals in mind.
3- Private practice owners the established business guys who are looking to grow their business;
4- Many eye care professionals are MBA holders they may have learned a little bit about entrepreneurship during their MBA studies.
Use the sample cover above and the suggestions that follow as a guide:
1- The cover should be very simple leaving an empty space somewhere to sign the book;
2- The Title and author name should use a modern font;
3- The cover should provide info about what's inside the book through illustrations, for example:
a- Gears: illustrating entrepreneur growth mindset (or anything more explicit)
b- Spectacles, sunglasses, lenses, eye drops, or any other eye care-related correction tools illustrating eye care (or anything more explicit)
c- Symbols illustrating ideas, opportunity, and profit, like money, charts, light bulbs, brain, and coins,...(or anything more explicit)
d- Entrepreneurship illustrated by Briefcase, tie, suit,... (or anything more explicit)

The rest is your creativity and imagination interplay.

Target Market(s)

Eye care professionals: Opticians, Optometrists, Ophthalmologists, Eye Care Administrators, Students in eye specialties.

Industry/Entity Type

eye care

Requirements
Must have
• 1- The cover should be very simple leaving an empty space somewhere to sign the book; 2- The Title and author name should use a modern font; 3- The cover should provide info about what's inside the book through illustrations, for example: a- Gears: illustrating entrepreneur growth mindset (or anything more explicit) b- Spectacles, sunglasses, lenses, eye drops, or any other eye care-related correction tools illustrating eye care (or anything more explicit) c- Symbols illustrating ideas, opportunity, and profit, like money, charts, light bulbs, brain, and coins,...(or anything more explicit) d- Entrepreneurship illustrated by Briefcase, tie, suit,... (or anything more explicit)

```html
<!DOCTYPE html>
<html lang="en">
<head>
<meta charset="utf-8">
<title>The Lens Practice Builder – Book Cover</title>
<link href="https://fonts.googleapis.com/css2?family=Bebas+Neue&family=Montserrat:wght@400&family=Roboto+Condensed:wght@700&display=swap" rel="stylesheet">
<style>
  :root {
    --frame-grey: #3d3d3d;
    --cover-blue: #d3e6ea;
    --ink: #050505;
    --case-dark: #151515;
    --case-mid: #3b4041;
    --case-shadow: rgba(0, 0, 0, 0.28);
  }
  * { margin: 0; padding: 0; box-sizing: border-box; }
  html, body {
    width: 840px;
    height: 1200px;
    overflow: hidden;
    background: var(--frame-grey);
  }
  .cover {
    position: absolute;
    left: 56px;
    top: 61px;
    width: 720px;
    height: 1079px;
    background: var(--cover-blue);
    color: var(--ink);
  }
  .cover-title {
    position: absolute;
    top: 67px;
    left: 40px;
    right: 40px;
    text-align: center;
    font-family: "Bebas Neue", "Oswald", sans-serif;
    font-weight: 400;
    font-size: 97px;
    line-height: 102px;
    letter-spacing: 2.5px;
  }
  .cover-title span { display: block; white-space: nowrap; }
  .cover-subtitle {
    position: absolute;
    top: 366px;
    left: 0;
    width: 100%;
    text-align: center;
    font-family: "Montserrat", "Helvetica Neue", sans-serif;
    font-weight: 400;
    font-size: 27px;
    letter-spacing: 0.4px;
  }
  .briefcase-art {
    position: absolute;
    left: 166px;
    top: 527px;
    width: 400px;
    height: 310px;
  }
  .cover-author {
    position: absolute;
    top: 1024px;
    left: 0;
    width: 100%;
    text-align: center;
    font-family: "Roboto Condensed", "Arial Narrow", sans-serif;
    font-weight: 700;
    font-size: 37px;
    transform: translateY(-50%);
  }
</style>
</head>
<body>
  <main class="cover">
    <h1 class="cover-title">
      <span>The Lens Practice</span>
      <span>Builder</span>
    </h1>
    <p class="cover-subtitle">How to launch with confidence</p>

    <svg class="briefcase-art" viewBox="0 0 400 310" role="img" aria-label="Photograph of a black leather briefcase with a silver clasp and top handle">
      <defs>
        <radialGradient id="caseShade" cx="50%" cy="62%" r="70%">
          <stop offset="0%" stop-color="var(--case-mid)"/>
          <stop offset="100%" stop-color="var(--case-dark)"/>
        </radialGradient>
        <radialGradient id="groundShadow" cx="50%" cy="50%" r="50%">
          <stop offset="0%" stop-color="var(--case-shadow)"/>
          <stop offset="100%" stop-color="var(--case-shadow)" stop-opacity="0"/>
        </radialGradient>
      </defs>
      <ellipse cx="200" cy="300" rx="200" ry="9" fill="url(#groundShadow)"/>
      <rect x="5" y="34" width="390" height="264" rx="14" fill="url(#caseShade)"/>
    </svg>

    <p class="cover-author">Rufus Tembley, Optom, MBA, DBA, EIC</p>
  </main>
</body>
</html>
```